Business card for law firm

Need business card for new law firm. Think confident, authoritative, conservative, but not stuffy or old-fashioned.

Contact Information for Business Card

Content for card - logo (uploaded), plus the following:

Paul Whitcombe (larger font)
Managing Partner (larger font, but not as large as name)
Level 9, 7 Ferris Lane
Sydney NSW 2000
Main Tel 02 9364 2710
Direct Tel 02 8472 3159
Email paul@qvlegal.com.au
www.qvlegal.com.au

Letterhead design should include logo plus:
Level 9, 7 Ferris Lane
Sydney NSW 2000
Tel 02 8472 3159
www.qvlegal.com.au

```html
<!DOCTYPE html>
<html lang="en">
<head>
<meta charset="utf-8">
<title>Quayvale Lawyers – Business Card</title>
<link rel="stylesheet" href="https://fonts.googleapis.com/css2?family=Cinzel:wght@400;500&family=Open+Sans:wght@400&display=swap">
<style>
  :root {
    --navy: #031a55;
    --white: #ffffff;
    --ink: #111111;
    --backdrop: #5b5b5b;
  }
  * { margin: 0; padding: 0; box-sizing: border-box; }
  html, body { width: 1200px; height: 802px; overflow: hidden; }
  body { background: var(--backdrop); position: relative; font-family: "Open Sans", sans-serif; }

  .card {
    position: absolute;
    top: 274px;
    width: 442px;
    height: 265px;
    background: var(--white);
    overflow: hidden;
    box-shadow: 0 3px 8px rgba(0,0,0,0.45);
  }
  .card--contact { left: 136px; }
  .card--brand { left: 624px; }

  .contact-panel {
    position: absolute;
    left: 51px;
    top: 0;
    right: 0;
    bottom: 0;
    background: var(--navy);
  }

  .contact-details {
    position: absolute;
    right: 23px;
    top: 64px;
    text-align: right;
    color: var(--white);
    font-size: 12.5px;
    line-height: 16px;
  }
  .contact-name {
    font-family: "Cinzel", serif;
    font-weight: 500;
    font-size: 18px;
    line-height: 19px;
    letter-spacing: 0.2px;
    text-transform: uppercase;
  }
  .contact-role { font-size: 13px; line-height: 15px; margin-bottom: 7px; }
  .contact-line { display: flex; justify-content: flex-end; align-items: center; gap: 3px; }
  .contact-line .label { font-size: 10px; }
  .contact-address { margin-top: 3px; font-size: 13px; }
  .icon { width: 9px; height: 9px; flex: none; }

  .brand {
    position: absolute;
    left: 0; right: 0;
    top: 64px;
    text-align: center;
    color: var(--ink);
  }
  .brand-square {
    width: 46px; height: 46px;
    margin: 0 auto 24px;
    background: var(--navy);
  }
  .brand-name {
    font-family: "Cinzel", serif;
    font-size: 36px;
    line-height: 36px;
    letter-spacing: 1px;
  }
  .brand-tagline {
    font-family: "Cinzel", serif;
    font-size: 12px;
    letter-spacing: 13px;
    margin-top: 2px;
    padding-left: 13px;
  }
</style>
</head>
<body>

<section class="card card--contact">
  <div class="contact-panel"></div>
  <div class="contact-details">
    <div class="contact-name">Paul Whitcombe</div>
    <div class="contact-role">Managing Partner</div>
    <div class="contact-line">02 9364 2710
      <svg class="icon" viewBox="0 0 10 10"><path fill="#fff" d="M1,3 C1,1 9,1 9,3 V4 H7 V3 H3 V4 H1 Z M2,5 H8 L9,9 H1 Z"/></svg>
    </div>
    <div class="contact-line">02 8472 3159 <span class="label">(DIRECT)</span>
      <svg class="icon" viewBox="0 0 10 10"><path fill="#fff" d="M1,3 C1,1 9,1 9,3 V4 H7 V3 H3 V4 H1 Z M2,5 H8 L9,9 H1 Z"/></svg>
    </div>
    <div class="contact-line">paul@qvlegal.com.au
      <svg class="icon" viewBox="0 0 10 10"><rect x="0.5" y="2" width="9" height="6.5" fill="#fff"/><path d="M0.5,2 L5,5.5 L9.5,2" fill="none" stroke="var(--navy)" stroke-width="1"/></svg>
    </div>
    <div class="contact-line">www.qvlegal.com.au
      <svg class="icon" viewBox="0 0 10 10"><circle cx="5" cy="5" r="4.5" fill="#fff"/><path d="M3,3 L5,4 L4,6 Z M6,6 L7,7" stroke="var(--navy)" stroke-width="1" fill="var(--navy)"/></svg>
    </div>
    <div class="contact-address">Level 9, 7 Ferris Lane<br>Sydney NSW 2000</div>
  </div>
</section>

<section class="card card--brand">
  <div class="brand">
    <div class="brand-square"></div>
    <div class="brand-name">QUAYVALE</div>
    <div class="brand-tagline">LAWYERS</div>
  </div>
</section>

</body>
</html>
```